Zielgruppe
Wir verkaufen in unserem Onlineshop alles zum Thema Wohnen mit dem Schwerpunkt Möbel. Die Hauptzielgruppe ist zwischen 25 und 45 Jahren.
Aufgabenstellung
Wir bevorzugen ein modernes, flaches und aufgeräumtes Design ähnlich wie kranu.de / pelvix31.de mit dem Fokus auf Preisaggressivität und Rabatte.
- Das Grundlayout muss so bleiben, wie es aktuell ist. Natürlich dürfen einzelne Elemente verschoben / versetzt werden.
- Im Header sollte Platz für eine kleine Werbefläche sein (ähnlich wie der konfigurierbare Kleiderschrank).
- Der Shop basiert auf Tervano 1.9.
- Die Rabatte in den Produktdetailseiten müssen genauso aufgebaut sein
- Die Suche sollte in den Header platziert werden und nicht im Menü
- Ein SSL Logo soll im Header platziert weden
- Die Vorteile (Kostenloser Versand, Sicher einkaufen, Kauf auf Rechnung) sollen im Header erscheinen
- Das Design sollte responsive sein
Es wird nur das reine Design ohne Programmierung benötigt.

```html
<!DOCTYPE html>
<html lang="de">
<head>
<meta charset="utf-8">
<title>moebelwelt7 – Startseite</title>
<link href="https://fonts.googleapis.com/css2?family=Open+Sans:wght@300;400;600;700&family=Roboto:wght@400;500&display=swap" rel="stylesheet">
<style>
:root{
  --green:#7ab03a;
  --teal:#3aa0b8;
  --nav-active:#4aa8c5;
  --magenta:#b0104f;
  --text:#222;
  --muted:#555;
  --line:#e3e3e3;
  --topbar:#f5f5f5;
}
*{box-sizing:border-box;margin:0;padding:0}
html,body{width:764px;height:1200px;overflow:hidden;background:#fff}
body{position:relative;font-family:"Open Sans",sans-serif;color:var(--text)}
.abs{position:absolute}

.topbar{left:0;top:0;width:764px;height:55px;background:var(--topbar)}
.phone-icon{left:107px;top:16px}
.phone-number{left:134px;top:14px;font-size:12.5px;font-weight:600;color:var(--teal);letter-spacing:.2px}
.phone-hours{left:134px;top:29px;font-size:7.5px;color:var(--text)}
.promo{left:270px;top:0;width:227px;height:49px;background:#fff;border-radius:0 0 4px 4px}
.promo-percent{left:39px;top:6px;font-size:28px;font-weight:600;color:var(--green);line-height:1}
.promo-title{left:97px;top:9px;font-size:10px;line-height:1}
.promo-sub{left:97px;top:20px;font-size:6.5px;color:var(--muted)}
.promo-cta{left:97px;top:29px;font-size:7px;font-weight:700;color:var(--green);letter-spacing:.3px}
.seal{top:7px;width:27px;height:27px;border-radius:50%;background:#bdbdbd;border:2px solid #e6e6e6;box-shadow:0 0 0 1px #aaa}
.seal-sq{top:7px;width:18px;height:25px;border-radius:3px;background:#c9c9c9}
.security-line{left:537px;top:42px;width:111px;height:1px;background:#ddd}
.security-label{left:556px;top:38px;width:74px;height:10px;background:var(--green);color:#fff;font-size:5.5px;font-weight:700;text-align:center;line-height:10px;border-radius:1px}

.logo{left:108px;top:84px;display:flex;align-items:center;gap:6px}
.logo-mark{width:14px;height:14px;background:var(--green)}
.logo-name{font-size:21px;font-weight:700;color:var(--green);letter-spacing:-.3px}
.search{left:269px;top:87px;width:228px;height:25px;border:1px solid #ddd;border-radius:2px;display:flex;align-items:center;padding-left:9px;gap:6px;font-size:9.5px;color:#666}
.icon-sep{top:86px;width:1px;height:26px;background:#eee}
.cart-count{left:641px;top:81px;width:16px;height:16px;border-radius:50%;background:var(--teal);color:#fff;font-size:10px;font-weight:700;text-align:center;line-height:16px}

.nav{left:0;top:142px;width:764px;height:36px;border-top:1px solid var(--line)}
.nav-item{top:0;height:36px;line-height:36px;font-family:"Roboto",sans-serif;font-size:7.5px;color:#111;text-transform:uppercase}
.nav-item.active{background:var(--nav-active);color:#fff;text-align:center}

.hero{left:0;top:178px;width:764px;height:289px;background:linear-gradient(90deg,#8d8d8b 0%,#a7a6a3 35%,#b2b1ae 60%,#9c9b98 100%)}
.hero-title{left:139px;top:37px;font-size:29px;font-weight:700;color:#fff;line-height:33px;letter-spacing:-.2px}
.btn{background:var(--green);color:#fff;font-family:"Roboto",sans-serif;font-weight:500;text-align:center}
.hero-btn{left:139px;top:122px;width:124px;height:31px;line-height:31px;font-size:12px}
.round-arrow{width:19px;height:19px;border-radius:50%;background:#fff;display:flex;align-items:center;justify-content:center}
.dot{top:267px;width:9px;height:9px;border-radius:50%;border:1.5px solid #fff}
.dot.on{background:var(--green);border-color:var(--green)}

.benefit-text{top:507px;font-size:9.5px;font-weight:400}
.benefit-sep{top:497px;width:1px;height:30px;background:#ddd}

.tile{top:561px;width:270px;height:188px;border-radius:2px}
.tile-title{font-size:15px;font-weight:700;color:#fff;line-height:20px}
.tile-btn{width:106px;height:31px;line-height:31px;font-size:11.5px}

.section-title{left:107px;top:780px;font-size:19.5px;font-weight:300;letter-spacing:.2px}
.nav-circle{top:780px;width:30px;height:30px;border-radius:50%;border:1px solid #ddd;display:flex;align-items:center;justify-content:center}

.product{top:823px;width:130px}
.product-img{width:130px;height:89px}
.badge{left:-4px;top:-4px;width:34px;height:34px;border-radius:50%;background:var(--magenta);color:#fff;font-family:"Roboto",sans-serif;font-size:9.5px;font-weight:500;text-align:center;line-height:34px}
.product-name{left:8px;top:100px;width:118px;font-size:8px;font-weight:300;color:#333;line-height:10.5px}
.price-old{left:8px;top:143px;font-size:7px;color:#444;text-decoration:line-through}
.price-new{left:8px;top:152px;font-family:"Roboto",sans-serif;font-size:12.5px;color:var(--magenta)}

.kids{left:108px;top:1030px;width:550px;height:190px;border:1px solid #eee;overflow:hidden}
.kids-photo{right:0;top:0;width:300px;height:190px;background:linear-gradient(90deg,#ffffff 0%,#f1ece4 30%,#e8d8c5 60%,#c9dce8 100%)}
.kids-title{left:33px;top:22px;font-size:19px;font-weight:400}
.kids-text{left:35px;top:54px;width:220px;font-size:9.5px;font-weight:300;line-height:13.5px;color:#444}
.kids-price{left:34px;top:100px;font-size:31px;font-weight:400;color:var(--teal)}
.kids-btn{left:35px;top:152px;width:106px;height:31px;line-height:33px;font-size:11.5px}
</style>
</head>
<body>

<!-- Top bar -->
<div class="abs topbar"></div>
<svg class="abs phone-icon" width="22" height="22" viewBox="0 0 22 22" aria-hidden="true">
  <circle cx="11" cy="11" r="10" fill="none" stroke="#3aa0b8" stroke-width="1.4"/>
  <path d="M7.2 6.2c.6-.5 1.3-.3 1.6.3l.9 1.6c.3.5.1 1-.3 1.3l-.6.4c.5 1.3 1.6 2.5 2.9 3l.5-.6c.3-.4.9-.5 1.3-.2l1.6 1c.5.3.6 1 .2 1.5l-.8.8c-1 1-4 .3-6.2-1.9S5.4 8 6.4 7z" fill="none" stroke="#3aa0b8" stroke-width="1.3"/>
</svg>
<div class="abs phone-number">0481 / 27 66 41 90</div>
<div class="abs phone-hours">Mo-Fr 9-21 Uhr Sa 10-15 Uhr</div>

<div class="abs promo">
  <div class="abs promo-percent">10%</div>
  <div class="abs promo-title">Kleiderschrank Jetzt</div>
  <div class="abs promo-sub">auch selbst Zusammenstellen</div>
  <div class="abs promo-cta">EINFÜHRUNGSRABATTE</div>
</div>

<div class="abs seal" style="left:538px"></div>
<div class="abs seal" style="left:582px"></div>
<div class="abs seal-sq" style="left:628px"></div>
<div class="abs security-line"></div>
<div class="abs security-label">GUARANTEED SECURITY</div>

<!-- Header -->
<div class="abs logo"><span class="logo-mark"></span><span class="logo-name">moebelwelt7</span></div>
<div class="abs search">
  <svg width="11" height="11" viewBox="0 0 11 11" aria-hidden="true"><circle cx="4.6" cy="4.6" r="3.7" fill="none" stroke="#555" stroke-width="1.2"/><path d="M7.4 7.4l2.8 2.8" stroke="#555" stroke-width="1.2"/></svg>
  <span>Suche...</span>
</div>
<svg class="abs" style="left:531px;top:89px" width="20" height="20" viewBox="0 0 20 20" aria-label="Konto"><circle cx="10" cy="6.5" r="4.5" fill="none" stroke="#222" stroke-width="1.3"/><path d="M2 18.5c0-3 2.5-5 5-5.5h6c2.5.5 5 2.5 5 5.5z" fill="none" stroke="#222" stroke-width="1.3"/></svg>
<div class="abs icon-sep" style="left:564px"></div>
<svg class="abs" style="left:580px;top:89px" width="20" height="20" viewBox="0 0 20 20" aria-label="Angebote"><path d="M2 2h7l9 9-7 7-9-9z" fill="none" stroke="#222" stroke-width="1.3" stroke-linejoin="round"/><circle cx="6" cy="6" r="1.3" fill="none" stroke="#222" stroke-width="1.1"/></svg>
<div class="abs icon-sep" style="left:613px"></div>
<svg class="abs" style="left:621px;top:89px" width="26" height="22" viewBox="0 0 26 22" aria-label="Warenkorb"><path d="M1 2h4l3 11h13l3-8H7" fill="none" stroke="#222" stroke-width="1.3" stroke-linejoin="round"/><circle cx="10" cy="18" r="1.8" fill="none" stroke="#222" stroke-width="1.2"/><circle cx="19" cy="18" r="1.8" fill="none" stroke="#222" stroke-width="1.2"/></svg>
<div class="abs cart-count">3</div>

<!-- Navigation -->
<nav class="abs nav">
  <div class="abs nav-item" style="left:108px">Wohnen</div>
  <div class="abs nav-item active" style="left:160px;width:75px">Schlafen</div>
  <div class="abs nav-item" style="left:255px">Kinder-Baby</div>
  <div class="abs nav-item" style="left:341px">Essen</div>
  <div class="abs nav-item" style="left:402px">Kuche</div>
  <div class="abs nav-item" style="left:465px">Bis 60% Rabatt</div>
  <div class="abs nav-item" style="left:561px">Sonstiges</div>
  <div class="abs nav-item" style="left:638px;top:-1px">Sale</div>
</nav>

<!-- Hero slider -->
<section class="abs hero" role="img" aria-label="Helles Schlafzimmer mit Doppelbett, Kleiderschrank und Steinwand">
  <h1 class="abs hero-title">Matratzen mit Komfort<br>für mehr Schlafqualität</h1>
  <div class="abs btn hero-btn">40% GESPART</div>
  <div class="abs round-arrow" style="left:52px;top:135px"><svg width="8" height="8" viewBox="0 0 8 8"><path d="M7 4H1.5M3.5 1.5L1 4l2.5 2.5" fill="none" stroke="#222" stroke-width="1"/></svg></div>
  <div class="abs round-arrow" style="left:693px;top:135px"><svg width="8" height="8" viewBox="0 0 8 8"><path d="M1 4h5.5M4.5 1.5L7 4 4.5 6.5" fill="none" stroke="#222" stroke-width="1"/></svg></div>
  <div class="abs dot" style="left:358px"></div>
  <div class="abs dot on" style="left:371px"></div>
  <div class="abs dot" style="left:384px"></div>
  <div class="abs dot" style="left:397px"></div>
</section>

<!-- Benefits -->
<svg class="abs" style="left:127px;top:500px" width="32" height="26" viewBox="0 0 32 26" aria-hidden="true"><rect x="14" y="2" width="17" height="13" rx="1" fill="none" stroke="#3aa0b8" stroke-width="1.6"/><path d="M1 20v-7l4-5h8v12z" fill="#3aa0b8"/><rect x="14" y="17" width="17" height="3" fill="#3aa0b8"/><circle cx="6" cy="21.5" r="2.5" fill="#fff" stroke="#3aa0b8" stroke-width="1.5"/><circle cx="24" cy="21.5" r="2.5" fill="#fff" stroke="#3aa0b8" stroke-width="1.5"/></svg>
<div class="abs benefit-text" style="left:180px">Kostenloser Versand</div>
<div class="abs benefit-sep" style="left:294px"></div>
<svg class="abs" style="left:326px;top:498px" width="24" height="29" viewBox="0 0 24 29" aria-hidden="true"><path d="M6 10V6a6 6 0 0 1 12 0v4" fill="none" stroke="#3aa0b8" stroke-width="1.8"/><rect x="2" y="10" width="20" height="17" rx="2" fill="none" stroke="#3aa0b8" stroke-width="1.8"/><path d="M7 18l4 4 7-7" fill="none" stroke="#3aa0b8" stroke-width="2"/></svg>
<div class="abs benefit-text" style="left:382px">Sicher einkaufen</div>
<div class="abs benefit-sep" style="left:494px"></div>
<svg class="abs" style="left:520px;top:499px" width="27" height="27" viewBox="0 0 27 27" aria-hidden="true"><rect x="2" y="2" width="19" height="22" rx="2" fill="none" stroke="#3aa0b8" stroke-width="1.8"/><path d="M6 8h11M6 12h11M6 16h7" stroke="#3aa0b8" stroke-width="1.6"/><path d="M2 21h23v3a2 2 0 0 1-2 2H4a2 2 0 0 1-2-2z" fill="#3aa0b8"/></svg>
<div class="abs benefit-text" style="left:565px">Kauf auf Rechnung</div>

<!-- Promo tiles -->
<div class="abs tile" style="left:108px;background:linear-gradient(90deg,#6c5a4c 0%,#c9a679 35%,#e9c8a4 55%,#b7b1a5 80%,#5b6a85 100%)" role="img" aria-label="Lächelnde Frau vor einem offenen Kleiderschrank mit bunten Kleidern">
  <div class="abs tile-title" style="left:23px;top:91px">Ihr ganz persönlicher<br>Kleiderschrank</div>
  <div class="abs btn tile-btn" style="left:24px;top:140px">40% GESPART</div>
</div>
<div class="abs tile" style="left:388px;background:linear-gradient(90deg,#2b2b2b 0%,#4a4a48 40%,#9a9c98 70%,#505050 100%)" role="img" aria-label="Wohnraum mit schwarzem Ledersessel vor hohen Industriefenstern">
  <div class="abs tile-title" style="left:23px;top:91px">Ihr ganz persönlicher<br>Kleiderschrank</div>
  <div class="abs btn tile-btn" style="left:23px;top:140px">40% GESPART</div>
</div>

<!-- Topseller -->
<h2 class="abs section-title">UNSERE TOPSELLER</h2>
<div class="abs nav-circle" style="left:590px"><svg width="10" height="9" viewBox="0 0 10 9"><path d="M9 4.5H1.5M4.5 1.5L1.2 4.5 4.5 7.5" fill="none" stroke="#444" stroke-width="1"/></svg></div>
<div class="abs nav-circle" style="left:628px"><svg width="10" height="9" viewBox="0 0 10 9"><path d="M1 4.5h7.5M5.5 1.5l3.3 3-3.3 3" fill="none" stroke="#444" stroke-width="1"/></svg></div>

<div class="abs product" style="left:108px">
  <div class="product-img" style="background:linear-gradient(180deg,#e6e8ea 0%,#cfd2d3 50%,#3a3a3a 75%,#e0d27a 100%)" role="img" aria-label="Schwarzes Boxspringbett in hellem Raum"></div>
  <div class="abs badge">-36%</div>
  <div class="abs product-name">Wohnlandschaft, in Mikrofaser Vintage-Look braun</div>
  <div class="abs price-old">999,00 €</div>
  <div class="abs price-new">575,10 €</div>
</div>
<div class="abs product" style="left:248px">
  <div class="product-img" style="background:linear-gradient(180deg,#6e5a48 0%,#b49a78 45%,#62c7cf 65%,#c9b28c 100%)" role="img" aria-label="Schlafzimmer mit Holzbett und türkiser Bettwäsche"></div>
  <div class="abs badge">-27%</div>
  <div class="abs product-name">Schlafzimmerkombination 4-tlg. in Eiche-Dekor mit Abs. in Lavagrau</div>
  <div class="abs price-old">999,00 €</div>
  <div class="abs price-new">575,10 €</div>
</div>
<div class="abs product" style="left:388px">
  <div class="product-img" style="background:linear-gradient(90deg,#8fa3ab 0%,#c3d5dc 40%,#eef0f0 60%,#7f8487 100%)" role="img" aria-label="Weißer Esstisch mit grauen Schwingstühlen"></div>
  <div class="abs badge">-12%</div>
  <div class="abs product-name">Boxspringbett schwarz, Feinstrukturstoff</div>
  <div class="abs price-old">999,00 €</div>
  <div class="abs price-new">575,10 €</div>
</div>
<div class="abs product" style="left:528px">
  <div class="product-img" style="background:linear-gradient(180deg,#f2f0ee 0%,#e8e4e0 45%,#7a4a38 70%,#5a3328 100%)" role="img" aria-label="Braunes Sofa vor heller Wand mit Bilderrahmen"></div>
  <div class="abs badge">-34%</div>
  <div class="abs product-name">Boxspringbett schwarz, Feinstrukturstoff</div>
  <div class="abs price-old">999,00 €</div>
  <div class="abs price-new">575,10 €</div>
</div>

<!-- Kids banner -->
<section class="abs kids">
  <div class="abs kids-photo" role="img" aria-label="Lachendes Mädchen mit Mutter im Kinderzimmer"></div>
  <h2 class="abs kids-title">Kindgerecht und schön!</h2>
  <p class="abs kids-text">Entdecken Sie unsere kindgerechten Baby- und Kinderzimmer und zaubern Sie ihren Kleinen ein wundervolles Lächeln ins Gesicht!</p>
  <div class="abs kids-price">445,47 €</div>
  <div class="abs btn kids-btn">40% GESPART</div>
</section>

</body>
</html>
```